Equipment Finance Specialist I work with companies who need the funds to buy their equipment

I would like a business card that stands out on the shelves. I want to be able to hand it to someone and say WOW. This card should have my logo.
You can put color into it I am very open on design and color

What my company does is we deal with dealerships that sell equipment such as Dump Trucks garbage trucks tractors trailers. Customers get referred to us and depending on their time in business we will ask for the following items

Companies that have been in business for more than two years we have a credit application program up to 250K . With this program we need the following items Credit application filled out(which is what I would like to be able for the customer to click on my website to get.) as well as three current month bank statements.

Deals over 250k we will need the following items

2 years business tax returns
2 years personal tax returns
Profit & Loss statement
Personal Financial Statement

what we do
100% FINANCING
SEASONAL PAYMENTS
LOAN BALLOON PAYMENTS
TRAC LEASING
LOW-INTEREST REFINANCING RATES
DEBT CONSOLIDATION

We specialize in creative financing solutions and offer a variety of reliable, flexible and expandable lending choices.

Target Market(s)

Trucking Companies

Industry/Entity Type

Trucking Company

Contact Information for Business Card

* $250,000 Application only Program
* Loans from $30,000 to 5,000,000
* Competitive Interest Rates

Font styles to use
Serif
Sans Serif

Colors

Designer to choose colors to be used in the design.

Requirements
Must have
• On the back of the card.
• * $250,000 Application only Program
• * Loans from $30,000 to 5,000,000
• My name, email, website. address
• * Competitive Interest Rates
• * 100% Financing
Nice to have
• I want my logo to pop on the card
• My logo is the great one I would like to use
Should not have
• I am up for your creativity as well

```html
<!DOCTYPE html>
<html lang="en">
<head>
<meta charset="UTF-8">
<title>Summit Lending – Business Card</title>
<link href="https://fonts.googleapis.com/css2?family=Archivo+Black&family=Open+Sans:wght@400;600&display=swap" rel="stylesheet">
<style>
  :root {
    --navy: #1f2d66;
    --navy-deep: #17235a;
    --red: #e3202e;
    --white: #ffffff;
    --ink: #1b2a5c;
    --backdrop: #4a4a4c;
    --rule: rgba(255,255,255,0.45);
  }
  * { box-sizing: border-box; margin: 0; padding: 0; }
  html, body { width: 1200px; height: 880px; overflow: hidden; }
  body {
    background: var(--backdrop);
    font-family: "Open Sans", sans-serif;
    position: relative;
  }
  .card {
    position: absolute;
    width: 560px;
    height: 320px;
    border-radius: 22px;
    overflow: hidden;
    box-shadow: 0 14px 30px rgba(0,0,0,0.35);
  }

  /* Front */
  .card-front {
    left: 60px; top: 70px;
    background: var(--navy);
    border-bottom: 8px solid var(--red);
  }
  .crane-art {
    position: absolute;
    left: 0; top: 0;
    width: 230px; height: 210px;
    background: linear-gradient(135deg, rgba(255,255,255,0.08), rgba(255,255,255,0.02));
  }
  .brand {
    position: absolute;
    left: 0; right: 0; top: 78px;
    display: flex; align-items: center; justify-content: center; gap: 18px;
  }
  .brand-dot {
    width: 74px; height: 74px; border-radius: 50%;
    background: var(--white);
  }
  .brand-name {
    font-family: "Archivo Black", sans-serif;
    color: var(--white);
    font-size: 46px;
    line-height: 1;
    letter-spacing: 1px;
    text-transform: uppercase;
  }
  .front-rule {
    position: absolute; left: 34px; right: 34px; top: 200px;
    height: 1px; background: var(--rule);
  }
  .features {
    position: absolute; left: 40px; right: 30px; top: 218px;
    list-style: none;
    display: grid; grid-template-columns: 1fr 1fr; row-gap: 10px; column-gap: 20px;
    color: var(--white); font-size: 15px;
  }
  .features li { display: flex; align-items: center; gap: 10px; }
  .features li::before {
    content: ""; width: 8px; height: 8px; border-radius: 50%;
    background: var(--red); flex-shrink: 0;
  }

  /* Back */
  .card-back {
    left: 580px; top: 490px;
    background: var(--white);
  }
  .back-mark {
    position: absolute; left: 60px; top: 90px;
    width: 140px; height: 140px; border-radius: 50%;
    background: var(--navy);
  }
  .divider {
    position: absolute; left: 250px; width: 2px;
  }
  .divider-red { top: 56px; height: 36px; background: var(--red); }
  .divider-navy { top: 112px; height: 150px; background: var(--navy); }
  .contact {
    position: absolute; left: 272px; top: 46px;
    color: var(--ink);
  }
  .contact-name {
    font-family: "Archivo Black", sans-serif;
    font-size: 28px; line-height: 1; color: var(--navy);
  }
  .contact-role { font-size: 16px; margin-top: 4px; }
  .contact-address { font-size: 16px; margin-top: 16px; line-height: 1.3; }
  .contact-lines { list-style: none; margin-top: 10px; font-size: 16px; }
  .contact-lines li { display: flex; align-items: center; gap: 10px; line-height: 1.5; }
  .contact-lines svg { width: 14px; height: 14px; flex-shrink: 0; }
</style>
</head>
<body>

<section class="card card-front">
  <div class="crane-art" role="img" aria-label="Faint illustration of a crane arm"></div>
  <div class="brand">
    <span class="brand-dot"></span>
    <span class="brand-name">Summit Lending</span>
  </div>
  <div class="front-rule"></div>
  <ul class="features">
    <li>$250,000 Application only Program</li>
    <li>Loans from $30,000 to 5,000,000</li>
    <li>Competitive Interest Rates</li>
    <li>100% Financing</li>
  </ul>
</section>

<section class="card card-back">
  <div class="back-mark" role="img" aria-label="Company emblem area"></div>
  <div class="divider divider-red"></div>
  <div class="divider divider-navy"></div>
  <div class="contact">
    <h1 class="contact-name">DANIEL REEVE</h1>
    <p class="contact-role">Founder &amp; CEO</p>
    <p class="contact-address">48 Harbour Row, Suite B<br>Leeds, UK LS1 4AX</p>
    <ul class="contact-lines">
      <li>
        <svg viewBox="0 0 16 16" aria-hidden="true"><path fill="#e3202e" d="M3 1l3 3-2 2c1 2 3 4 5 5l2-2 3 3-2 3C7 15 1 9 2 3z"/></svg>
        555 014 2288
      </li>
      <li>
        <svg viewBox="0 0 16 16" aria-hidden="true"><rect x="1" y="3" width="14" height="10" fill="#e3202e"/><path d="M1 3l7 6 7-6" stroke="#fff" stroke-width="1.4" fill="none"/></svg>
        hello@summitlending.com
      </li>
      <li>
        <svg viewBox="0 0 16 16" aria-hidden="true"><circle cx="8" cy="8" r="7" fill="#e3202e"/><path d="M1 8h14M8 1c-3 4-3 10 0 14M8 1c3 4 3 10 0 14" stroke="#fff" stroke-width="1" fill="none"/></svg>
        www.summitlending.com
      </li>
    </ul>
  </div>
</section>

</body>
</html>
```